Los Brava Dip – CPG Website with WordPress - Store Locator: WP Maps plugin

Larkfield Food Company is a startup consumer packaged goods (CPG) brand launching its flagship product line — Los Brava Dip. We’re seeking a talented web designer to create a bold, professional, mobile-optimized website using WordPress with a WP Maps store locator to help customers find local retailers.

Our goal is to build a strong online presence that supports both retail growth and direct-to-consumer sales.

See Los Brava _Website_Design_Brief word document.

The website URL is https://losbravadip.example/

Target Market(s)

Consumers of gourmet salsa

Industry/Entity Type

Consumer Packaged Goods - Salsa manufacturer.

Coding

Coded - Design and coding required

Number of Pages Required

5+ page

Requirements
Must have
• The design of the Los Brava Dip website shall emulate the clean, polished aesthetic of Fennigo.example.

```html
<!DOCTYPE html>
<html lang="en">
<head>
<meta charset="utf-8">
<title>Los Brava Dip</title>
<link href="https://fonts.googleapis.com/css2?family=Oswald:wght@400;500;700&family=Playfair+Display:wght@700;900&family=Lato:wght@400;700&display=swap" rel="stylesheet">
<style>
:root{
  --red:#c91f26;
  --deep-red:#921a1f;
  --cream:#fdf9e4;
  --dark:#2b2b2b;
  --orange:#bb7420;
  --pale-yellow:#f1e88a;
  --yellow:#fde200;
  --text:#333;
  --white:#fff;
}
*{box-sizing:border-box;margin:0;padding:0}
html,body{width:1200px;height:3380px;overflow:hidden}
body{position:relative;background:var(--cream);font-family:"Lato",sans-serif;color:var(--text)}
.abs{position:absolute}
.topbar{left:0;top:0;width:1200px;height:43px;background:var(--red);color:var(--white);font:500 15px "Oswald",sans-serif;text-align:center;line-height:43px;letter-spacing:.3px}
.header{left:0;top:43px;width:1200px;height:141px;background:var(--cream)}
.search{left:111px;top:88px;width:172px;height:27px;border-bottom:1px solid #bbb;font-size:13px;color:#555;padding-top:2px}
.search svg{position:absolute;right:2px;top:3px}
.logo{font:700 44px/1 "Oswald",sans-serif;color:var(--red)}
.header-logo{left:0;width:1200px;top:76px;text-align:center}
.header-icons{left:1022px;top:92px;display:flex;gap:26px}
.nav{left:101px;top:163px;width:998px;height:64px;background:#262626;clip-path:polygon(0 0,100% 0,97.5% 50%,100% 100%,0 100%,2.5% 50%);display:flex;justify-content:space-around;align-items:center;padding:0 50px;z-index:3}
.nav a{color:var(--white);font:400 17px "Oswald",sans-serif;text-decoration:none}
.nav a.active{color:#f3d774;font-weight:700}
.hero{left:0;top:184px;width:1200px;height:548px;background:radial-gradient(ellipse at 50% 55%,#d7e4a4 0%,#b2cc74 40%,#8fae52 75%,#6f9440 100%)}
.hero-title{left:0;top:276px;width:1200px;text-align:center;font:700 68px/1 "Oswald",sans-serif;color:var(--red)}
.btn{display:block;text-align:center;font:500 17px "Oswald",sans-serif;border-radius:30px;text-decoration:none}
.shop-btn{left:525px;top:367px;width:149px;height:53px;line-height:53px;background:var(--white);color:var(--red);box-shadow:0 3px 0 var(--red)}
.jars{left:302px;top:459px;width:622px;height:407px;display:flex;align-items:flex-end;justify-content:center}
.jar{border-radius:40px 40px 60px 60px;box-shadow:0 8px 14px rgba(0,0,0,.25)}
.jar.red{width:220px;height:370px;background:linear-gradient(#c49a3c 0 12%,#c8382a 12%,#a8241e)}
.jar.green{width:240px;height:400px;background:linear-gradient(#c9a642 0 12%,#9dbb52 12%,#7c9a3a);margin:0 -30px;z-index:2}
.jar.orange{width:220px;height:370px;background:linear-gradient(#c49a3c 0 12%,#e9a33a 12%,#d1662c)}
.section-title{font:900 55px "Playfair Display",serif;text-align:center;display:flex;align-items:center;justify-content:center;gap:18px}
.dash{display:inline-flex;align-items:center}
.dash i{display:block;width:36px;height:3px;background:currentColor}
.dash b{display:block;width:12px;height:12px;border-radius:50%;background:currentColor}
.featured-title{left:0;top:905px;width:1200px;color:var(--red)}
.featured-title .dash{color:var(--dark)}
.card{top:1053px;width:272px;height:297px;border-radius:12px;text-align:center}
.card.verde{left:111px;background:linear-gradient(160deg,#a6c46a,#6f9a45)}
.card.natural{left:463px;width:275px;background:radial-gradient(circle at 50% 40%,#f7c55a,#e59b28);border:3px solid var(--red)}
.card.habanero{left:817px;background:linear-gradient(160deg,#e4a13a,#c9612e)}
.card-jar{position:absolute;left:50%;transform:translateX(-50%);top:26px;width:104px;height:164px;border-radius:22px 22px 30px 30px}
.card.natural .card-jar{top:-50px;width:150px;height:240px}
.card.verde .card-jar{background:linear-gradient(#c8a442 0 14%,#93b04a 14%,#6f8c36)}
.card.natural .card-jar{background:linear-gradient(#c8a442 0 14%,#d34a2a 14%,#e5a53a)}
.card.habanero .card-jar{background:linear-gradient(#c8a442 0 14%,#c8342a 14%,#9c2420)}
.card h3{position:absolute;top:212px;width:100%;font:700 19px "Playfair Display",serif;color:#2d2d2d}
.card.natural h3{top:209px}
.card .stars{position:absolute;top:244px;width:100%;font-size:14px;color:#222;letter-spacing:1px}
.card.natural .stars{top:241px}
.card .btn{position:absolute;left:50%;transform:translateX(-50%);top:275px;width:110px;height:43px;line-height:43px;color:var(--white);box-shadow:0 3px 0 rgba(0,0,0,.35)}
.card.natural .btn{top:272px}
.verde .btn{background:#3b5d2b}
.natural .btn{background:var(--red)}
.habanero .btn{background:#c4561f}
.reviews{left:0;top:1458px;width:1200px;height:607px;background:linear-gradient(#55804a,#4a7240)}
.reviews-title{left:0;top:1515px;width:1200px;color:var(--white)}
.reviews-panel{left:52px;top:1622px;width:1089px;height:358px;background:var(--white);border-radius:14px;box-shadow:6px 6px 0 rgba(40,60,30,.6)}
.review{width:302px;height:186px;background:var(--white);box-shadow:0 1px 8px rgba(0,0,0,.18);border-radius:4px;padding:16px 18px}
.review .stars{color:#f0a020;font-size:12px;letter-spacing:1px}
.review .head{display:flex;justify-content:space-between;align-items:baseline;margin-top:2px}
.review h4{font:700 17px "Lato",sans-serif;color:#222}
.review time{font-size:10px;color:#666}
.review p{font-size:15px;line-height:26px;margin-top:6px;color:#333}
.arrows{left:568px;top:1910px;display:flex;gap:22px}
.recipes{left:0;top:2065px;width:1200px;height:688px;background:var(--orange)}
.col-verde{left:650px;top:2065px;width:218px;height:688px;background:var(--pale-yellow)}
.col-natural{left:868px;top:2065px;width:219px;height:688px;background:var(--deep-red)}
.recipes-title{left:108px;top:2140px;font:900 55px/64px "Playfair Display",serif;color:var(--white)}
.recipes-title .dash{color:var(--white);margin-left:14px;vertical-align:middle}
.recipes-text{left:111px;top:2286px;width:300px;color:var(--white);font:700 16px/26px "Lato",sans-serif;white-space:nowrap}
.recipes-text p+p{margin-top:25px}
.learn-btn{left:111px;top:2491px;width:142px;height:52px;line-height:52px;background:var(--white);color:var(--orange);box-shadow:0 3px 0 rgba(0,0,0,.2)}
.timeline{left:500px;top:2188px}
.vert{font:900 52px/70px "Playfair Display",serif;transform:rotate(-90deg);transform-origin:center;white-space:nowrap;width:400px;text-align:center;left:-200px;top:2437px}
.vert.hab{margin-left:539px;color:#2b2118}
.vert.ver{margin-left:759px;color:#1d1d1d}
.vert.nat{margin-left:978px;color:var(--white)}
.instagram{left:0;top:2753px;width:1200px;height:184px;background:var(--yellow)}
.insta-title{left:0;top:2813px;width:1200px;color:var(--red);font-size:47px}
.insta-title .dash{color:#333}
.footer-logo{left:111px;top:3060px;font-size:48px}
.footer-col{top:3030px}
.footer-col h5{font:700 19px "Playfair Display",serif;color:var(--red);margin-bottom:4px}
.footer-col li{list-style:none;font-size:15px;line-height:30px;color:#333;padding-left:3px;display:flex;align-items:center;gap:8px}
.col-quick{left:387px}.col-help{left:627px}.col-contact{left:870px}
.divider{left:111px;top:3277px;width:977px;height:1px;background:#bbb}
.copy{left:0;top:3312px;width:1200px;text-align:center;font-size:15px;color:#333}
</style>
</head>
<body>
<div class="abs topbar">FREE SHIPPING INCLUDED &nbsp;|&nbsp; Boxes starting at $20</div>

<header class="abs header"></header>
<div class="abs search">Search
  <svg width="12" height="12" viewBox="0 0 12 12"><circle cx="5" cy="5" r="3.8" fill="none" stroke="#222" stroke-width="1.8"/><line x1="8" y1="8" x2="11" y2="11" stroke="#222" stroke-width="2"/></svg>
</div>
<div class="abs header-logo"><span class="logo">Los Brava</span></div>
<div class="abs header-icons">
  <svg width="20" height="18" viewBox="0 0 20 18"><path d="M0 1h4l3 10h10l2-7H6" fill="none" stroke="#111" stroke-width="2.4"/><circle cx="8" cy="15" r="2" fill="#111"/><circle cx="16" cy="15" r="2" fill="#111"/></svg>
  <svg width="16" height="18" viewBox="0 0 16 18"><circle cx="8" cy="5" r="4.5" fill="#111"/><path d="M0 18c0-6 3-8 8-8s8 2 8 8z" fill="#111"/></svg>
</div>

<nav class="abs nav">
  <a class="active" href="#">HOME</a><a href="#">ABOUT</a><a href="#">PRODUCT</a><a href="#">WHERE TO BUY</a><a href="#">RECIPE</a><a href="#">REVIEWS</a><a href="#">CONTACT US</a>
</nav>

<section class="abs hero" role="img" aria-label="Sunburst over green rolling hills landscape"></section>
<h1 class="abs hero-title">WHERE FLAVOR MEETS FIRE</h1>
<a class="abs btn shop-btn" href="#">SHOP NOW</a>
<div class="abs jars" role="img" aria-label="Three jars of Los Brava salsa: Habanero, Verde and All Natural">
  <div class="jar red"></div><div class="jar green"></div><div class="jar orange"></div>
</div>

<h2 class="abs section-title featured-title"><span class="dash"><i></i><b></b></span>FEATURED PRODUCT<span class="dash"><b></b><i></i></span></h2>

<div class="abs card verde">
  <div class="card-jar" role="img" aria-label="Jar of Verde salsa"></div>
  <h3>Los Brava - Verde</h3><div class="stars">★★★★★</div>
  <a class="btn" href="#">BUY NOW</a>
</div>
<div class="abs card natural">
  <div class="card-jar" role="img" aria-label="Jar of All Natural salsa"></div>
  <h3>Los Brava - All Natural</h3><div class="stars">★★★★★</div>
  <a class="btn" href="#">BUY NOW</a>
</div>
<div class="abs card habanero">
  <div class="card-jar" role="img" aria-label="Jar of Habanero salsa"></div>
  <h3>Los Brava - Habanero</h3><div class="stars">★★★★★</div>
  <a class="btn" href="#">BUY NOW</a>
</div>

<section class="abs reviews"></section>
<h2 class="abs section-title reviews-title"><span class="dash"><i></i><b></b></span>REVIEWS<span class="dash"><b></b><i></i></span></h2>
<div class="abs reviews-panel"></div>
<article class="abs review" style="left:111px;top:1678px">
  <div class="stars">★★★★★</div>
  <div class="head"><h4>Daniel Harwick</h4><time>12 April, 2025</time></div>
  <p>Very good, and I'm a salsa snob! Very nice overall. I cook a lot so I often make my own, but this is great! Awesome taste, fresh.</p>
</article>
<article class="abs review" style="left:448px;top:1672px">
  <div class="stars">★★★★★</div>
  <div class="head"><h4>Marta Olsen</h4><time>16 May, 2025</time></div>
  <p>Very good, and I'm a salsa snob! Very nice overall. I cook a lot so I often make my own, but this is great! Awesome taste, fresh.</p>
</article>
<article class="abs review" style="left:787px;top:1678px">
  <div class="stars">★★★★★</div>
  <div class="head"><h4>Stefan</h4><time>22 April, 2025</time></div>
  <p>Very good, and I'm a salsa snob! Very nice overall. I cook a lot so I often make my own, but this is great! Awesome taste, fresh.</p>
</article>
<div class="abs arrows">
  <svg width="16" height="24" viewBox="0 0 16 24"><path d="M13 2 3 12l10 10" fill="none" stroke="#555" stroke-width="2"/></svg>
  <svg width="16" height="24" viewBox="0 0 16 24"><path d="M3 2l10 10L3 22" fill="none" stroke="#555" stroke-width="2"/></svg>
</div>

<section class="abs recipes"></section>
<div class="abs col-verde"></div>
<div class="abs col-natural"></div>
<h2 class="abs recipes-title">OUR<br>RECIPES<span class="dash"><b></b><i></i></span></h2>
<div class="abs recipes-text">
  <p>Excepteur sint occaecat cupidatat non<br>proident, sunt in culpa qui quis nostrud<br>exercitation ullamco laboris</p>
  <p>Nisi ut aliquip ex ea commodo conse<br>quat officia deserunt mollit &nbsp;officia<br>anim id est laborum.</p>
</div>
<a class="abs btn learn-btn" href="#">LEARN MORE</a>
<svg class="abs timeline" width="520" height="80" viewBox="0 0 520 80">
  <rect x="39" y="34" width="440" height="10" fill="#fff"/>
  <circle cx="39" cy="39" r="39" fill="#fff"/>
  <circle cx="259" cy="39" r="39" fill="#fff"/>
  <circle cx="478" cy="39" r="39" fill="#fff"/>
  <ellipse cx="39" cy="41" rx="20" ry="9" fill="#c0631d"/>
  <ellipse cx="259" cy="41" rx="20" ry="9" fill="#efe27a"/>
  <ellipse cx="478" cy="41" rx="20" ry="9" fill="#b3161c"/>
</svg>
<div class="abs vert hab">HABANERO</div>
<div class="abs vert ver">VERDE</div>
<div class="abs vert nat">ALL NATURAL</div>

<section class="abs instagram"></section>
<h2 class="abs section-title insta-title"><span class="dash"><i></i><b></b></span>FOLLOW LOS BRAVA ON INSTAGRAM<span class="dash"><b></b><i></i></span></h2>

<div class="abs logo footer-logo">Los Brava</div>
<div class="abs footer-col col-quick">
  <h5>QUICK LINKS</h5>
  <ul><li>Home</li><li>About</li><li>Product</li><li>Where to Buy</li><li>Recipe</li><li>Contact Us</li></ul>
</div>
<div class="abs footer-col col-help">
  <h5>HELP LINKS</h5>
  <ul><li>FAQ</li><li>Term of Use</li><li>Privacy Policy</li><li>Support Links</li><li>Terms &amp; Conditions</li><li>Shipping Policy</li></ul>
</div>
<div class="abs footer-col col-contact">
  <h5>CONTACT US</h5>
  <ul>
    <li><svg width="10" height="14" viewBox="0 0 10 14"><path d="M5 0a5 5 0 0 0-5 5c0 4 5 9 5 9s5-5 5-9a5 5 0 0 0-5-5z" fill="#c91f26"/><circle cx="5" cy="5" r="2" fill="#fff"/></svg>Los Brava, United States</li>
    <li><svg width="12" height="12" viewBox="0 0 12 12"><path d="M2 0l3 3-1.5 2a7 7 0 0 0 3.5 3.5L9 7l3 3-2 2C5 12 0 7 0 2z" fill="#c91f26"/></svg>+1 555 010 0199</li>
    <li><svg width="14" height="10" viewBox="0 0 14 10"><rect width="14" height="10" fill="#c91f26"/><path d="M0 0l7 5 7-5" fill="none" stroke="#fff" stroke-width="1.2"/></svg>support@losbravadip.example</li>
  </ul>
</div>
<div class="abs divider"></div>
<div class="abs copy">Copyrights@2025.Los Brava.All Rights Reserved</div>
</body>
</html>
```